New Business Cards for Tormin Group

We need a new Business Card to compliment our new logo. We are a vibrant design, manufacture and install business providing recreation areas, public parks and Municipal spaces. We want business cards that are classy, modern and clean.

We have recently changed our logo, and are celebrating our 40th anniversary. We want business cards with a new modern design to reflect our status.

Target Market(s)

Customers

Contact Information for Business Card

We need all the details of our 3 offices as per the business card attached. Please disregard the old logo on the business card, the other three files show our new logo.

Requirements
Must have
• All info as per attached business card but with new logo.
Nice to have

```html
<!DOCTYPE html>
<html lang="en">
<head>
<meta charset="utf-8">
<title>Tormin Group – Business Card</title>
<link href="https://fonts.googleapis.com/css2?family=Roboto:wght@400;700;900&display=swap" rel="stylesheet">
<style>
  :root{
    --stage:#1d1d21;
    --red:#ec3237;
    --charcoal:#4a4a4d;
    --ink:#2b2b2d;
    --text:#3a3a3c;
    --paper:#ffffff;
  }
  *{margin:0;padding:0;box-sizing:border-box}
  html,body{width:1200px;height:800px;overflow:hidden}
  body{background:var(--stage);font-family:"Roboto",Arial,sans-serif;position:relative}
  .card{position:absolute;top:245px;width:540px;height:310px;box-shadow:0 18px 40px rgba(0,0,0,.5)}
  /* front */
  .card-front{left:40px;background:var(--red);display:flex;align-items:center;justify-content:center;gap:16px}
  .brand-dot{width:64px;height:64px;border-radius:50%;background:var(--paper)}
  .brand-name{color:var(--paper);font-weight:900;font-size:40px;letter-spacing:1px;text-transform:uppercase}
  /* back */
  .card-back{left:620px;background:var(--paper);display:flex;overflow:hidden}
  .side-band{width:112px;background:var(--charcoal);border-right:5px solid var(--red);position:relative}
  .side-name{position:absolute;left:50%;top:50%;transform:translate(-50%,-50%) rotate(-90deg);white-space:nowrap;color:var(--paper);font-weight:900;font-size:30px;letter-spacing:1px;text-transform:uppercase}
  .details{flex:1;position:relative;padding:26px 22px 0 24px;color:var(--text);font-size:10.5px;line-height:1.32}
  .person-name{font-weight:700;font-size:16px;color:var(--ink)}
  .person-role{color:var(--red);font-size:11.5px;position:relative}
  .person-role::after{content:"";position:absolute;left:110px;right:-22px;top:8px;height:1px;background:var(--red)}
  .direct{margin-top:8px}
  .direct-row{display:flex;align-items:center;gap:7px;font-size:11px;margin-bottom:3px}
  .direct-row svg{width:13px;height:13px;flex:none}
  .offices{display:grid;grid-template-columns:1fr 1fr;column-gap:16px;margin-top:12px}
  .office{margin-bottom:10px}
  .office-title{color:var(--red);font-weight:700;font-size:12px;margin-bottom:1px}
  .web{position:absolute;right:22px;bottom:20px;font-weight:700;font-size:11px;letter-spacing:2px;color:var(--ink)}
  .web span{color:var(--red)}
</style>
</head>
<body>
  <section class="card card-front" aria-label="Card front">
    <div class="brand-dot"></div>
    <div class="brand-name">Tormin Group</div>
  </section>

  <section class="card card-back" aria-label="Card back">
    <div class="side-band"><div class="side-name">Tormin Group</div></div>
    <div class="details">
      <div class="person-name">Omar Haddadin</div>
      <div class="person-role">Managing Partner</div>
      <div class="direct">
        <div class="direct-row">
          <svg viewBox="0 0 14 14"><circle cx="7" cy="7" r="7" fill="var(--red)"/><rect x="4.5" y="3" width="5" height="8" rx="1" fill="none" stroke="#fff" stroke-width="1.2"/></svg>
          +971 (0)50 418 7720
        </div>
        <div class="direct-row">
          <svg viewBox="0 0 14 14"><circle cx="7" cy="7" r="7" fill="var(--red)"/><rect x="3.5" y="4.5" width="7" height="5" fill="none" stroke="#fff" stroke-width="1.1"/><path d="M3.5 4.5 7 7.5 10.5 4.5" fill="none" stroke="#fff" stroke-width="1.1"/></svg>
          omar@tormingroup.com
        </div>
      </div>
      <div class="offices">
        <div>
          <div class="office">
            <div class="office-title">Head Office</div>
            P.O. Box: 40218 Abu Dhabi, U.A.E.<br>
            Tel No: +971 (0)2 5173390<br>
            Fax No: +971 (0)2 5173391<br>
            Email: sales@tormingroup.com
          </div>
          <div class="office">
            <div class="office-title">Qatar Office</div>
            P.O. Box: 27731 Doha, Qatar<br>
            Tel No: +974 44385120<br>
            Fax No: +974 44385121<br>
            Email: sales@tormingroup.com
          </div>
        </div>
        <div>
          <div class="office">
            <div class="office-title">Dubai Office</div>
            P.O. Box: 581064 Dubai, U.A.E.<br>
            Tel No: +971 (0)4 3806642<br>
            Fax No: +971 (0)4 3806643<br>
            Email: sales@tormingroup.com
          </div>
        </div>
      </div>
      <div class="web">www.<span>tormingroup</span>.com</div>
    </div>
  </section>
</body>
</html>
```